Life Coaching Business Needs A Business card Design

Earthy, quirky, colourful business card needed for a Life Coaching company supporting same sex attracted young men. My coaching supports these same sex attracted guys to find their own inner happiness and passion and purpose and not feel they need to live a 'label' or follow the crowd. It its about personal passion and happiness.
IT IS ABOUT THEIR INNER RAINBOW.
Some aspects of rainbow would be important to the design.

I have uploaded a recently designed POSTCARD and the business card will be a smaller version with much less information. The Business Card will take the very important parts of the POSTCARD

Front of Card.......
I'm thinking the front of the card would need to be the large LOGO with a rainbow emerging from the inside...from the heart...the core. This will almost FILL the front of the card. This has been uploaded for you. IMMEDIATELY under the LOGO ( to make it a part of the logo) would be the words COACHING * WELLNESS *
The statement HAPPINESS and WHOLENESS for MEN WHO DATE MEN should feature across the front of the BUSINESS CARD as it does across the back of the POSTCARD. It will need some kind of rainbow background to the statement as it does on the POSTCARD. Needs to be a different rainbow pattern. See what you think.

That could be the front. On a black background.
I wonder what you think and what you will do with that.

Back Of Card.

I'm hoping the back of the BUSINESS card could be the PHOTO section from the back of the POSTCARD. The photo and the quote. I will make the quote shorter to fit better on a BUSINESS card. It can be written in a handwriting style to make it look like a personal message from me as it is on the POSTCARD.

All across the top of the back of the card could be the statement
MOTIVATION and INSPIRATION for MEN WHO DATE MEN

Across the card under the statement would be the three contacts
www.brightvolume.com *0437 615 203*tom@brightvolume.com

It would be great to see if you have a different idea for this arrangement.

At the bottom of the Business card ( as on the photo at on the POSTCARD ) would be my name with a description underneath

Tom Walbrook
Transformational Life Coach * Happiness Guru * Change catalyst

What do you think ? Will all of this work ?
I hope I haven't been too prescriptive. I don't want this to be a boring job for you.

Looking forward to hearing what you think and seeing what you come up with.

Target Market(s)

Same sex attracted males. All ages. Especially those who are struggling or unhappy or depressed. The card must be uplifting and it must SPEAK to these guys. I want ti include a personal 'quote' from me ( in handwriting font as if I wrote to them ) to encourage these guys to get the help they need.

Industry/Entity Type

Business

Contact Information for Business Card

I have been quite prescriptive but am happy to see what the designer might come up with as well. I don't mean to make it boring for the designer. I have included names and contact details in the brief. Please let me know if I need to give you more details.

Requirements
Must have
• LOGO
• A clear statement on the front and back to state clearly who the coaching service is for. I have explained these in the brief.
• Pic of me to fill the back of the card with room to write the details on. I have other pics if needed.
• Needs to be casual and inviting. Almost informal and organic. Quite earthy to balance with the 'lifestyle' these guys can often live.
Nice to have
• Colour and ideas to keep it uncluttered.
Should not have
• Formal design or 'business' like feel.

```html
<!DOCTYPE html>
<html lang="en">
<head>
<meta charset="utf-8">
<title>Tom Walbrook – Coaching Business Card</title>
<link rel="stylesheet" href="https://fonts.googleapis.com/css2?family=Cabin:wght@500;600;700&family=Reenie+Beanie&display=swap">
<style>
  :root {
    --stage: #2b2e33;
    --card: #0b0b0b;
    --ink: #1e1e1e;
    --white: #ffffff;
    --violet: #7a6cb3;
    --indigo: #5a78bd;
    --blue: #3a80c2;
    --teal: #1f9a86;
    --green: #3da54a;
    --lime: #b4c22a;
    --yellow: #f0c21a;
    --orange: #ef8a1f;
    --red: #df4826;
    --sky-top: #e9edee;
    --sky-low: #f8f6ee;
    --grass-light: #7fa23a;
    --grass-dark: #3c6419;
  }
  * { margin: 0; padding: 0; box-sizing: border-box; }
  html, body { width: 1200px; height: 900px; overflow: hidden; }
  body { background: var(--stage); position: relative; font-family: "Cabin", sans-serif; }

  .card {
    position: absolute; left: 78px; top: 140px;
    width: 1049px; height: 600px;
    background: var(--card);
  }
  .audience-line, .services-line {
    position: absolute; left: 47px; width: 953px;
    font-weight: 600; letter-spacing: 0.5px; white-space: nowrap;
    display: flex; justify-content: space-between;
  }
  .audience-line { top: 32px; font-size: 27px; }
  .services-line { top: 534px; font-size: 23px; }
  .services-line .dot { color: var(--white); margin: 0 2px; }

  .photo {
    position: absolute; left: 47px; top: 72px; width: 953px; height: 455px;
    background: linear-gradient(to bottom, var(--sky-top) 0%, var(--sky-low) 74%, var(--grass-light) 80%, var(--grass-dark) 100%);
  }
  .contact-row {
    position: absolute; left: 14px; right: 14px; top: 8px;
    display: flex; justify-content: space-between;
    font-size: 27px; font-weight: 500; color: var(--ink);
  }
  .quote {
    position: absolute; left: 115px; top: 62px; width: 620px;
    font-family: "Reenie Beanie", cursive;
    font-size: 50px; line-height: 48px; color: var(--ink);
  }
  .coach-name {
    position: absolute; left: 16px; bottom: 14px;
    font-size: 38px; font-weight: 700; letter-spacing: 1px;
    color: var(--white);
    -webkit-text-stroke: 6px var(--ink); paint-order: stroke fill;
  }

  .c-indigo { color: var(--indigo); } .c-violet { color: var(--violet); }
  .c-blue { color: var(--blue); } .c-teal { color: var(--teal); }
  .c-green { color: var(--green); } .c-lime { color: var(--lime); }
  .c-yellow { color: var(--yellow); } .c-orange { color: var(--orange); }
  .c-red { color: var(--red); }
</style>
</head>
<body>
  <section class="card">
    <h1 class="audience-line">
      <span><span class="c-indigo">COACHING</span> <span class="c-violet">AND</span> <span class="c-blue">SUPPORT</span> <span class="c-green">FOR</span> <span class="c-lime">SAME</span> <span class="c-yellow">SEX</span> <span class="c-orange">ATTRACTED</span> <span class="c-red">GUYS</span></span>
    </h1>

    <div class="photo" role="img" aria-label="Photo of the coach standing barefoot on a green grassy field under a bright sky">
      <div class="contact-row">
        <span>www.brightvolume.com</span>
        <span>0437 615 203</span>
        <span>tom@brightvolume.com</span>
      </div>
      <p class="quote">“My Coaching is about helping to change whatever is making you unhappy or unwell. If you’re not happy, something has to change. If there’s something to change, I can help”</p>
      <p class="coach-name">TOM WALBROOK</p>
    </div>

    <p class="services-line">
      <span><span class="c-indigo">PERSONAL CHANGE</span><span class="dot"> • </span><span class="c-teal">RELATIONSHIPS</span><span class="dot"> • </span><span class="c-yellow">HAPPINESS</span><span class="dot">•</span><span class="c-orange">MINDFULNESS</span> <span class="c-red">COACH</span></span>
    </p>
  </section>
</body>
</html>
```